Marlowby Services Website Design

We have most content but require a professional design. We have a logo already and will need it utilized along with several of the photos from the attached documentation.
First page should have our mission and Vision and the synapsis provided in the word document. Visitors will be prompted to select from one of our 3 divisions from this page.
Each division will have the same list of tabs : About, Services, Safety, Careers and Contact.
Photos on each divisions page should be representative of the divisions offerings. The word doc attached contains the requested content and we are open to edits that would complement and fill the website.
I like the Quorvane site www.quorvane.example - they are our competition so cant be modeled directly after this.
Please include prompts to request quote at each service page. align the format of the geotechnical page to the other 2 divisions.
I used chat gpt for some of the content so will need it optimized for SCO.

```html
<!DOCTYPE html>
<html lang="en">
<head>
<meta charset="utf-8">
<title>Marlowby Oil And Gas Services</title>
<link href="https://fonts.googleapis.com/css2?family=Poppins:wght@400;500;600&display=swap" rel="stylesheet">
<style>
  :root {
    --red: #e3262e;
    --red-soft: #fde3e5;
    --ink: #111111;
    --body: #3c3c3c;
    --white: #ffffff;
    --footer-bg: #fcf0f1;
    --rule: #c9c4c5;
  }
  * { margin: 0; padding: 0; box-sizing: border-box; }
  html, body { width: 721px; height: 1200px; overflow: hidden; background: var(--white); }
  body { font-family: "Poppins", sans-serif; color: var(--ink); position: relative; }
  .abs { position: absolute; }

  /* Hero */
  .hero { left: 0; top: 0; width: 721px; height: 318px;
    background: linear-gradient(105deg, #3e4a35 0%, #56603f 30%, #6e6c55 55%, #8a8a86 75%, #9a9b98 100%); }
  .hero-shade { left: 0; top: 0; width: 721px; height: 318px;
    background: linear-gradient(90deg, rgba(0,0,0,.45) 0%, rgba(0,0,0,.15) 60%, rgba(0,0,0,0) 100%); }
  .brand-hero { left: 85px; top: 10px; font-weight: 600; font-size: 17px; letter-spacing: 1.5px; color: var(--white); }
  .hero-title { left: 85px; top: 102px; width: 290px; font-weight: 500; font-size: 28px; line-height: 36px; color: var(--white); }
  .division-label { left: 85px; top: 189px; font-size: 10.5px; color: var(--white); }
  .division-list { left: 85px; top: 214px; list-style: none; }
  .division-list li { display: flex; align-items: center; height: 19.2px; font-size: 8.6px; font-weight: 500; color: var(--white); }
  .division-list a { color: var(--white); text-decoration: underline; margin-left: 7px; }

  /* Section heading */
  .section-title { font-weight: 500; font-size: 17.5px; color: var(--ink); }
  .underline { height: 1px; width: 45px; background: var(--red); }

  /* Services */
  .service { width: 110px; text-align: center; top: 433px; }
  .service-icon { width: 42px; height: 42px; border-radius: 50%; background: var(--red-soft); margin: 0 auto; display: flex; align-items: center; justify-content: center; }
  .service-label { margin-top: 11px; font-size: 8.4px; font-weight: 500; line-height: 11.8px; color: var(--ink); }

  .copy { font-size: 7.7px; line-height: 13.6px; color: var(--body); }
  .copy p + p { margin-top: 8px; }

  /* Footer */
  .footer { left: 0; top: 1048px; width: 721px; height: 152px; background: var(--footer-bg); }
  .brand-footer { left: 0; width: 721px; top: 1075px; text-align: center; font-weight: 600; font-size: 18px; letter-spacing: 1.5px; color: var(--red); }
  .contacts { left: 0; width: 721px; top: 1119px; display: flex; justify-content: center; gap: 30px; font-size: 7.3px; color: var(--ink); }
  .contacts div { display: flex; align-items: center; gap: 7px; }
  .footer-rule { left: 85px; top: 1166px; width: 551px; height: 1px; background: var(--rule); }
  .copyright { left: 85px; top: 1177px; font-size: 7.5px; font-weight: 500; color: var(--ink); }
  .socials { left: 556px; top: 1175px; display: flex; gap: 7px; }
  .socials span { width: 15px; height: 15px; border-radius: 50%; background: var(--red); }
</style>
</head>
<body>

<header>
  <div class="abs hero" role="img" aria-label="Aerial photo of a boom truck with extended mast beside a road and parked pickup trucks"></div>
  <div class="abs hero-shade"></div>
  <div class="abs brand-hero">MARLOWBY</div>
  <h1 class="abs hero-title">Marlowby Oil And Gas Services</h1>
  <p class="abs division-label">Select Division:</p>
  <ul class="abs division-list">
    <li><svg width="13" height="6" viewBox="0 0 13 6"><path d="M0 3h12M9 0.5L12 3 9 5.5" stroke="#fff" stroke-width="0.9" fill="none"/></svg><a href="#">Aerial Access</a></li>
    <li><svg width="13" height="6" viewBox="0 0 13 6"><path d="M0 3h12M9 0.5L12 3 9 5.5" stroke="#fff" stroke-width="0.9" fill="none"/></svg><a href="#">Geotechnical Drilling</a></li>
    <li><svg width="13" height="6" viewBox="0 0 13 6"><path d="M0 3h12M9 0.5L12 3 9 5.5" stroke="#fff" stroke-width="0.9" fill="none"/></svg><a href="#">Renewable Energy Services</a></li>
  </ul>
</header>

<section class="services">
  <h2 class="abs section-title" style="left:0;width:721px;text-align:center;top:369px;">Our Services</h2>
  <div class="abs underline" style="left:338px;top:396px;"></div>

  <div class="abs service" style="left:81px;">
    <div class="service-icon"><svg width="26" height="26" viewBox="0 0 26 26" fill="none" stroke="#e3262e" stroke-width="1.1"><path d="M3 8l9-4 9 4-9 4z M3 8v10l9 4V12 M21 8v4"/><circle cx="19" cy="18" r="4.5"/><path d="M17 18l1.5 1.5 2.5-3"/></svg></div>
    <p class="service-label">Delivering Safe</p>
  </div>
  <div class="abs service" style="left:193px;">
    <div class="service-icon"><svg width="26" height="26" viewBox="0 0 26 26" fill="none" stroke="#e3262e" stroke-width="1.1"><circle cx="14" cy="8" r="4"/><circle cx="14" cy="8" r="1.5"/><path d="M3 16h4v7H3z M7 17h6l3 2h5l2 2-6 2H7"/></svg></div>
    <p class="service-label">Reliable Aerial Access And Maintenance Services To Oil&amp;Gas</p>
  </div>
  <div class="abs service" style="left:305px;">
    <div class="service-icon"><svg width="26" height="26" viewBox="0 0 26 26" fill="none" stroke="#e3262e" stroke-width="1.1"><path d="M8 4v19M11 4v19M4 6h20M8 10h3M8 16h3M5 23h9M20 6v7M17 16h6l-3-3z"/></svg></div>
    <p class="service-label">Construction</p>
  </div>
  <div class="abs service" style="left:419px;">
    <div class="service-icon"><svg width="26" height="26" viewBox="0 0 26 26" fill="none" stroke="#e3262e" stroke-width="1.1"><path d="M5 3v4M8 3v4M4 7h5v4H4z M6.5 11v8h4 M11 14l6-5 6 5v9H11z M17 14l-2 4h3l-2 4"/></svg></div>
    <p class="service-label">Utility</p>
  </div>
  <div class="abs service" style="left:530px;">
    <div class="service-icon"><svg width="26" height="26" viewBox="0 0 26 26" fill="none" stroke="#e3262e" stroke-width="1.1"><path d="M8 9l5-5 5 5z M10 9v4M16 9v4 M3 20c4-6 8-6 10-2s6 2 10-4 M5 15l2 2M21 8c2 2 2 5 0 7-2-2-2-5 0-7z"/></svg></div>
    <p class="service-label">Renewable Energy Industries</p>
  </div>
</section>

<section class="vision">
  <div class="abs photo" style="left:110px;top:592px;width:196px;height:135px;background:linear-gradient(160deg,#8e8d80 0%,#6f7064 45%,#5e6358 100%);" role="img" aria-label="Aerial photo of a raised boom truck sign over a small town"></div>
  <h2 class="abs section-title" style="left:349px;top:603px;">Our Vision</h2>
  <div class="abs underline" style="left:349px;top:629px;"></div>
  <div class="abs copy" style="left:349px;top:646px;width:275px;">
    <p>To be the leading provider of aerialaccess, geotechnical drilling, and service solutions, setting the standard forexcellence in safety, efficiency, and environmental stewardship.</p>
  </div>
  <div class="abs photo" style="left:580px;top:700px;width:141px;height:56px;background:linear-gradient(180deg,#eeeeee 0%,#d6d6d6 50%,#3a3a3a 100%);" role="img" aria-label="Side view of a white boom truck"></div>
</section>

<section class="mission">
  <h2 class="abs section-title" style="left:85px;top:823px;">Our Mission</h2>
  <div class="abs underline" style="left:85px;top:849px;"></div>
  <div class="abs copy" style="left:85px;top:866px;width:295px;">
    <p>AtMarlowby, our mission is to deliver unparalleled aerial access, geotechnicaldrilling, and service and maintenance solutions, consistently exceeding ourclients' expectations. We strive to achieve this by investing in cutting-edgetechnology, fostering a culture of safety and continuous improvement, andprioritizing environmental sustainability.</p>
    <p>Through collaboration, integrity, anddedication, we aim to contribute to the success of our clients whilemaintaining the highest standards of quality and professionalism.</p>
  </div>
  <div class="abs photo" style="left:413px;top:809px;width:196px;height:183px;background:linear-gradient(180deg,#3f7fd0 0%,#6ea2e0 55%,#8f8c86 78%,#6c6a66 100%);" role="img" aria-label="Boom truck parked beneath a water tower under a blue sky"></div>
</section>

<footer>
  <div class="abs footer"></div>
  <div class="abs brand-footer">MARLOWBY</div>
  <div class="abs contacts">
    <div><svg width="10" height="8" viewBox="0 0 10 8"><rect width="10" height="8" rx="1" fill="#e3262e"/><path d="M0.8 1l4.2 3 4.2-3" stroke="#fff" stroke-width="0.8" fill="none"/></svg>info@marlowby.example</div>
    <div><svg width="10" height="10" viewBox="0 0 10 10"><path d="M2 0.5l2 2-1.2 1.3c.6 1.3 1.6 2.3 2.9 2.9L7 5.5l2 2-1.3 1.8C4.5 9 1 5.5.7 1.8z" fill="#e3262e"/></svg>555-010-4821</div>
    <div><svg width="10" height="11" viewBox="0 0 10 11"><path d="M5 0.5a3.5 3.5 0 0 1 3.5 3.5C8.5 6.5 5 9 5 9S1.5 6.5 1.5 4A3.5 3.5 0 0 1 5 .5z" fill="none" stroke="#e3262e" stroke-width="0.9"/><circle cx="5" cy="4" r="1.2" fill="#e3262e"/><ellipse cx="5" cy="10" rx="4" ry="0.8" fill="none" stroke="#e3262e" stroke-width="0.6"/></svg>88 Ridge Road Fernvale AB T0X-1B0</div>
  </div>
  <div class="abs footer-rule"></div>
  <p class="abs copyright">© 2024 Marlowby. All Rights Reserved.</p>
  <div class="abs socials"><span></span><span></span><span></span><span></span></div>
</footer>

</body>
</html>
```